Fresh, modern, fun business card for pediatric dental practice

Need a business card for fresh, modern, fun pediatric dental practice

Clean look that matches our website's font and colors

We prefer the look of curved corners on business cards

Target Market(s)

parents (mothers) of young children, professionals, mid-high class

Industry/Entity Type

Dental

Contact Information for Business Card

Maplebrook Pediatric Dentistry
482 Quarry Lane
Suite 517
Linden Hollow, PA 10987
717.555.0193
www.maplebrooksmiles.example

Mei-Ran Tsai, DMD
Corinne Walbeck, DMD
(we are working on our email address, but we would like that on the card as well)

Font styles to use
Sans Serif

Requirements
Must have
• All info; we would also like to make cards for individual staff members
• colors from our website and color palatte, attatched
• use same font and design as website for branding
Nice to have
• clean, simple card that has a pop of color
• we would like to see a few designs with our tag line "where smiles get brighter"
• we are not sure if we want to have it on there or not
• we would like to see a few designs incorporating the ribbon graphic on our website where the word WELCOME is

```html
<!DOCTYPE html>
<html lang="en">
<head>
<meta charset="utf-8">
<title>Maplebrook Pediatric Dentistry – Business Card</title>
<link href="https://fonts.googleapis.com/css2?family=Work+Sans:wght@400;500;600&display=swap" rel="stylesheet">
<style>
  :root {
    --backdrop: #d8c6b5;
    --card: #f7f6f3;
    --brand-gold: #e0ad1c;
    --ink: #2f2f31;
    --ink-soft: #4a4a4d;
  }
  html, body {
    margin: 0;
    padding: 0;
    width: 1200px;
    height: 900px;
    overflow: hidden;
    background: var(--backdrop);
  }
  .canvas {
    position: relative;
    width: 1200px;
    height: 900px;
    display: flex;
    align-items: center;
    justify-content: center;
  }
  .business-card {
    position: relative;
    width: 440px;
    height: 780px;
    background: var(--card);
    border-radius: 6px;
    font-family: "Work Sans", Arial, sans-serif;
    color: var(--ink);
    text-align: center;
    box-sizing: border-box;
  }
  .brand {
    position: absolute;
    top: 70px;
    left: 0;
    right: 0;
    color: var(--brand-gold);
    font-weight: 500;
  }
  .brand-dot {
    display: block;
    width: 64px;
    height: 64px;
    margin: 0 auto 22px;
    border-radius: 50%;
    background: var(--brand-gold);
  }
  .brand-name {
    margin: 0;
    font-size: 50px;
    font-weight: 500;
    line-height: 1.05;
    letter-spacing: 0.5px;
  }
  .brand-tagline {
    margin: 6px 0 0;
    font-size: 27px;
    font-weight: 500;
    letter-spacing: 1px;
  }
  .person {
    position: absolute;
    top: 458px;
    left: 0;
    right: 0;
  }
  .person-name {
    margin: 0;
    font-size: 28px;
    font-weight: 600;
    letter-spacing: 0.8px;
    color: var(--ink);
  }
  .person-title {
    margin: 4px 0 0;
    font-size: 19px;
    color: var(--ink-soft);
    letter-spacing: 0.5px;
  }
  .address {
    margin: 20px 0 0;
    font-size: 20px;
    line-height: 27px;
    color: var(--ink-soft);
    letter-spacing: 0.4px;
    font-style: normal;
  }
  .contact-icons {
    display: flex;
    justify-content: center;
    gap: 6px;
    margin-top: 24px;
  }
  .contact-icons svg {
    width: 14px;
    height: 14px;
    stroke: var(--ink-soft);
    fill: none;
    stroke-width: 1.6;
  }
  .contact-lines {
    margin: 18px 0 0;
    font-size: 20px;
    line-height: 27px;
    color: var(--ink-soft);
    letter-spacing: 0.3px;
  }
</style>
</head>
<body>
<main class="canvas">
  <article class="business-card">
    <header class="brand">
      <span class="brand-dot" aria-hidden="true"></span>
      <h1 class="brand-name">maplebrook</h1>
      <p class="brand-tagline">pediatric dentistry</p>
    </header>

    <section class="person">
      <h2 class="person-name">CORINNE WALBECK</h2>
      <p class="person-title">DMD</p>
      <address class="address">
        482 Quarry Lane<br>
        Suite 517 Linden Hollow, PA 10987
      </address>

      <div class="contact-icons" aria-hidden="true">
        <svg viewBox="0 0 16 16"><path d="M4 2l2.5 3-1.5 1.5c.8 2 2.5 3.7 4.5 4.5L11 9.5l3 2.5-1.5 2C7 13.5 2.5 9 2 3.5z"/></svg>
        <svg viewBox="0 0 16 16"><rect x="2" y="4" width="12" height="9"/><path d="M2 4l6 5 6-5"/></svg>
        <svg viewBox="0 0 16 16"><circle cx="8" cy="8" r="6"/><ellipse cx="8" cy="8" rx="2.6" ry="6"/><path d="M2 8h12"/></svg>
      </div>

      <p class="contact-lines">
        717.555.0193<br>
        hello@maplebrooksmiles.example<br>
        www.maplebrooksmiles.example
      </p>
    </section>
  </article>
</main>
</body>
</html>
```